High-end Oceanfront Real Estate Group Needs Clean, Modern Web Design

I’m looking for a clean, professional, modern and beautiful homepage web design for a Real Estate group in Southern California, USA.

The group/company is “Marwick on the Shore,” and they specialize in high end (i.e. expensive), oceanfront real estate in the Orange County area.

The look and feel of the page should accentuate the brand qualities: luxurious/expensive, professional, and beautiful (Orange County is one of the most beautiful areas in all the US and we would love the site to emphasize the beautiful beaches and scenery it has to offer).

Looks we like:
• www.brantleyhomesrealty.example
• www.closedbyvane.example -- I think the design is pretty out-dated in this site, but I like the organization/layout of the site

Header Tags (I don’t know if we can fit all of these, may need a side-menu, but I’d prefer header title only if possible):
• Welcome
• Featured Listings
• Previously Sold
• Sell
• Property Search
• Team
• Videos
• Blog
• Explore O.C.
• Contact

I have attached the beach and logo pics that we would like to use as the header, a few pictures of the team, and one sample home/view pic which can be used in any of the other sections (for pictures of the homes, just find expensive oceanfront houses and that will be fine).

I promise to provide feedback to each and every design submission. I appreciate the hard work that all of you are putting into your designs. There can be only one contest winner, but I hope to give all of you helpful feedback to submit the best designs possible!

Target Market(s)

Very wealthy home owners of oceanfront properties. These properties are worth several millions of dollars, and thus the site and brand needs to be targeted to very wealthy, successful individuals and families (both US and international buyers).

Industry/Entity Type

Real Estate

Number of Pages Required

2 page

Requirements
Must have
• I don’t want to give too many requirements, because I want to let you all be creative. However, here are the few Must Haves:
• Must submit 2 page designs (a home page and a sub page)
• Must use logo provided
• Focus is mostly on homes, but I would like to include some beach/ocean imagery as well
• The first “item” on the home page should be an accordion/slider which shows pictures of homes and with 1 line of text: “List with the Leader” and two link buttons: “Sell Your Home” and “Buy Your Home”
• Color palette needs to be mainly blues--to match ocean and sky blue
• Exported in all major formats (psd,ai,eps,png,jpeg,etc)
Nice to have
• We don’t necessarily need all of these, but would like to feature most:
• List of videos
• “Meet the Team”—brief team bios and pics
• Link(s) to Blog
• “List with the Leader” – section on why they should choose this firm
• Featured Listings
• Previously Sold

```html
<!DOCTYPE html>
<html lang="en">
<head>
<meta charset="utf-8">
<title>Marwick on the Shore — Welcome</title>
<link href="https://fonts.googleapis.com/css2?family=Open+Sans:wght@400;600;700&family=Raleway:wght@300;400;500&display=swap" rel="stylesheet">
<style>
:root{
  --header-bg:#e4e9fc;
  --accent:#6f93f2;
  --accent-dark:#4c6fd6;
  --ink:#333a44;
  --muted:#7b818a;
  --line:#e3e5ea;
  --band:#5b7fe0;
  --band-deep:#3f63c9;
  --sold-bg:#cdd5e6;
  --footer-bg:#1f1f21;
  --footer-text:#8a8d92;
  --white:#ffffff;
}
*{box-sizing:border-box;margin:0;padding:0}
html,body{width:1200px;height:2532px;overflow:hidden}
body{position:relative;font-family:"Open Sans",Arial,sans-serif;color:var(--ink);background:var(--white)}
section,header,footer{position:absolute;left:0;width:1200px}
.abs{position:absolute}

/* header */
.site-header{top:0;height:149px;background:var(--header-bg)}
.brand{left:96px;top:32px;display:flex;align-items:center;gap:12px}
.brand-mark{width:14px;height:14px;background:var(--accent)}
.brand-name{font-family:"Raleway",sans-serif;font-weight:300;font-size:30px;color:var(--accent);letter-spacing:1px;line-height:1}
.contact-line{right:99px;top:29px;display:flex;gap:36px;font-size:12px;color:#5d6470;align-items:center}
.contact-line span{display:flex;align-items:center;gap:8px}
.contact-line .phone{font-size:15px}
.main-nav{right:99px;top:96px;display:flex;gap:28px;font-size:11.5px;font-weight:600;color:#3e444e}
.main-nav .active{color:var(--accent)}

/* hero */
.hero{top:149px;height:459px;background:linear-gradient(180deg,#3b4a66 0%,#5c6678 35%,#7d7263 70%,#2f3a2a 100%)}
.hero-title{left:0;width:1200px;top:132px;text-align:center;font-family:"Raleway",sans-serif;font-weight:300;font-size:41px;color:var(--white);letter-spacing:1px}
.hero-actions{left:0;width:1200px;top:222px;display:flex;justify-content:center;gap:8px}
.btn-ghost{border:2px solid var(--white);color:var(--white);font-size:13px;padding:9px 12px;font-family:"Raleway",sans-serif}
.slide-arrow{top:211px;width:38px;height:34px;background:rgba(90,90,90,.75);display:flex;align-items:center;justify-content:center}
.slide-arrow.left{left:0}.slide-arrow.right{right:0}

/* welcome */
.welcome{top:608px;height:200px;text-align:center}
.welcome h1{margin-top:47px;font-family:"Raleway",sans-serif;font-weight:400;font-size:22px;line-height:32px;color:var(--ink)}
.welcome p{width:1004px;margin:19px auto 0;font-size:11.5px;line-height:21px;color:var(--muted)}

/* videos & blog */
.section-title{font-family:"Raleway",sans-serif;font-weight:400;font-size:22px;color:var(--ink)}
.media{top:808px;height:554px}
.videos-title{left:98px;top:30px}
.video-frame{left:98px;top:87px;width:569px;height:290px;background:linear-gradient(135deg,#e6e9ee,#c9cfd8 60%,#9aa2ad)}
.video-bar{left:0;bottom:0;width:100%;height:24px;background:#1d1d1d;display:flex;align-items:center;padding:0 8px;gap:12px;font-size:10px;color:#ccc}
.video-bar .progress{flex:1;height:3px;background:#555}
.play-btn{left:262px;top:128px;width:34px;height:30px;background:#c0232a;border-radius:6px}
.video-meta{left:98px;top:402px;display:flex;gap:26px;font-size:10.5px;color:var(--muted)}
.video-text{left:98px;top:434px;width:580px;font-size:11.5px;line-height:21px;color:var(--muted)}
.blog-title{left:748px;top:30px}
.blog-card{left:748px;width:354px;height:190px;border:1px solid var(--line);background:var(--white)}
.blog-card .thumb{left:10px;top:9px;width:154px;height:172px}
.blog-card h3{position:absolute;left:180px;top:13px;font-size:13.5px;font-weight:600;color:#3a3f48}
.blog-card p{position:absolute;left:180px;top:44px;width:162px;font-size:10.5px;line-height:20px;color:var(--muted);text-align:justify}
.blog-card .date{position:absolute;left:180px;top:158px;font-size:10px;color:var(--muted)}

/* featured */
.featured{top:1362px;height:377px;background:linear-gradient(180deg,var(--band) 0%,#6d8ee6 50%,var(--band-deep) 100%)}
.featured h2{position:absolute;top:40px;width:1200px;text-align:center;font-family:"Raleway",sans-serif;font-weight:400;font-size:22px;color:var(--white)}
.listing{top:105px;width:221px;height:157px}
.pager{left:533px;top:296px;display:flex}
.pager span{width:67px;height:33px;background:rgba(255,255,255,.18);display:flex;align-items:center;justify-content:center}

/* team */
.team{top:1739px;height:346px}
.team h2{left:98px;top:60px}
.team p{position:absolute;left:98px;top:100px;width:222px;font-size:11px;line-height:20px;color:#4a4f58;text-align:justify}
.btn-solid{left:98px;top:244px;width:213px;height:29px;background:var(--accent);color:var(--white);font-size:11.5px;display:flex;align-items:center;justify-content:center}
.portrait{top:65px;width:235px;height:208px}

/* sold */
.sold{top:2085px;height:275px;background:var(--sold-bg)}
.sold-col{top:0;width:480px}
.sold-col h2{position:absolute;top:42px;font-size:19px;font-weight:400;color:#3b414b;font-family:"Raleway",sans-serif}
.sold-col .rule{position:absolute;top:56px;height:1px;background:#b9c1d3}
.mini-nav{position:absolute;top:50px;display:flex;gap:3px}
.mini-nav i{width:12px;height:12px;border-radius:50%;background:#8a92a2;display:block}
.sold-col .avatar{position:absolute;top:96px;width:130px;height:130px;border-radius:50%}
.sold-col h3{position:absolute;top:96px;font-size:13.5px;font-weight:600;color:#3a3f48}
.sold-col .date{position:absolute;top:98px;font-size:10px;color:var(--muted)}
.sold-col p{position:absolute;top:126px;width:318px;font-size:11px;line-height:19px;color:#6c727c}

/* footer */
.site-footer{top:2360px;height:172px;background:var(--footer-bg);text-align:center}
.social{position:absolute;top:26px;width:1200px;display:flex;justify-content:center;gap:16px}
.social i{width:26px;height:26px;border-radius:50%;background:#5c5f64;display:block}
.footer-nav{position:absolute;top:96px;width:1200px;font-size:11px;color:var(--footer-text)}
.copyright{position:absolute;top:124px;width:1200px;font-size:10.5px;color:var(--footer-text)}
</style>
</head>
<body>

<header class="site-header">
  <div class="abs brand"><span class="brand-mark"></span><span class="brand-name">Marwick on the Shore</span></div>
  <div class="abs contact-line">
    <span><svg width="11" height="15" viewBox="0 0 11 15"><path d="M5.5 0A5.5 5.5 0 0 0 0 5.5C0 9.5 5.5 15 5.5 15S11 9.5 11 5.5A5.5 5.5 0 0 0 5.5 0Zm0 7.7a2.2 2.2 0 1 1 0-4.4 2.2 2.2 0 0 1 0 4.4Z" fill="#6f93f2"/></svg>18420 Tidewater Drive&nbsp; Laguna Beach, CA</span>
    <span class="phone"><svg width="14" height="14" viewBox="0 0 14 14"><path d="M3 0l2.4 3.2-1.5 1.7a8 8 0 0 0 5.2 5.2l1.7-1.5L14 11l-1.3 2.6C6 14 0 8 .4 1.3Z" fill="#6f93f2"/></svg><small style="font-size:12px">Call us :</small> 949.555.0184</span>
  </div>
  <nav class="abs main-nav">
    <span class="active">Welcome</span><span>Featured Listings</span><span>Previously Sold</span><span>Sell</span><span>Property Search</span><span>Team</span><span>Videos</span><span>Blog</span><span>Explore O.C.</span><span>Contact</span>
  </nav>
</header>

<section class="hero" role="img" aria-label="Luxury oceanfront villa at dusk with palm trees and lit terrace">
  <h2 class="abs hero-title">LIST WITH THE LEADER</h2>
  <div class="abs hero-actions"><span class="btn-ghost">SELL YOUR HOME</span><span class="btn-ghost">BUY YOUR HOME</span></div>
  <div class="abs slide-arrow left"><svg width="16" height="16" viewBox="0 0 16 16"><circle cx="8" cy="8" r="7.5" fill="#fff"/><path d="M9.5 4.5 6 8l3.5 3.5" stroke="#555" stroke-width="2" fill="none"/></svg></div>
  <div class="abs slide-arrow right"><svg width="16" height="16" viewBox="0 0 16 16"><circle cx="8" cy="8" r="7.5" fill="#fff"/><path d="M6.5 4.5 10 8l-3.5 3.5" stroke="#555" stroke-width="2" fill="none"/></svg></div>
</section>

<section class="welcome">
  <h1>WELCOME TO SOUTHERN CALIFORNIA AND LIVING<br>YOUR LIFE MARWICKONTHESHORE!</h1>
  <p>We at MarwickontheShore are privileged to help people from all over the world find their dream homes in Monarch Beach, Laguna Beach, Newport Coast, Dana Point, San Clemente and San Juan Capistrano.&nbsp; Whether you are buying or selling a property in Orange County, we want to help you in the most efficient, professional way possible.</p>
</section>

<section class="media">
  <h2 class="abs section-title videos-title">LIST OF VIDEOS</h2>
  <div class="abs video-frame" role="img" aria-label="Family smiling together in a bright modern living room">
    <div class="abs play-btn"><svg width="34" height="30" viewBox="0 0 34 30"><path d="M13 9v12l10-6z" fill="#fff"/></svg></div>
    <div class="abs video-bar"><svg width="10" height="10" viewBox="0 0 10 10"><path d="M1 0v10l8-5z" fill="#ccc"/></svg><span>0:00 / 1:47</span><span class="progress"></span><span style="width:18px;height:10px;background:#777;display:block"></span></div>
  </div>
  <div class="abs video-meta"><span>♥&nbsp; LIKE 1,2450</span><span>▪&nbsp; COMMENTS 0</span></div>
  <p class="abs video-text">The other hand, we denounce with righteous indignation and dislike men who are so beguiled and demoralized by the charms of pleasure of the moment, so blinded by desire, that they cannot foresee the pain and trouble that are bound to ensue; and equal blame belongs to those who fail in their duty</p>

  <h2 class="abs section-title blog-title">BLOG</h2>
  <article class="abs blog-card" style="top:85px">
    <div class="abs thumb" role="img" aria-label="Modern home interior lit at night" style="background:linear-gradient(135deg,#3a2f28,#8a6a4a 60%,#1e1a18)"></div>
    <h3>Voluptatem accusantium</h3>
    <p>Must explain to you how all this mistaken idea of denouncing pleasure and praising pain was plete account of the system, and dislikes, or avoids pleasure</p>
    <span class="date">▦&nbsp; 25 March 2015</span>
  </article>
  <article class="abs blog-card" style="top:298px">
    <div class="abs thumb" role="img" aria-label="Smiling family of four posing together" style="background:linear-gradient(135deg,#c9d3db,#d9b79c 55%,#8fa0b4)"></div>
    <h3>Voluptatem accusantium</h3>
    <p>Must explain to you how all this mistaken idea of denouncing pleasure and praising pain was plete account of the system, and dislikes, or avoids pleasure</p>
    <span class="date">▦&nbsp; 25 March 2015</span>
  </article>
</section>

<section class="featured">
  <h2>FEATURED LISTINGS</h2>
  <div class="abs listing" style="left:98px;background:linear-gradient(135deg,#d8d6d2,#8d6a52 60%,#3c3530)" role="img" aria-label="Open kitchen with wooden island"></div>
  <div class="abs listing" style="left:358px;background:linear-gradient(180deg,#6f8fc8,#a5764f 55%,#2b6fb8)" role="img" aria-label="Villa courtyard with pool at dusk"></div>
  <div class="abs listing" style="left:620px;background:linear-gradient(135deg,#e8e6e3,#c8beb3 55%,#7a4d32)" role="img" aria-label="Bright living room with hardwood floors"></div>
  <div class="abs listing" style="left:880px;background:linear-gradient(180deg,#2d4f86,#6a5440 60%,#1c1c1f)" role="img" aria-label="Modern house with lit terrace at night"></div>
  <div class="abs pager">
    <span><svg width="8" height="12" viewBox="0 0 8 12"><path d="M6.5 1 1.5 6l5 5" stroke="#fff" stroke-width="1.5" fill="none"/></svg></span>
    <span><svg width="8" height="12" viewBox="0 0 8 12"><path d="M1.5 1l5 5-5 5" stroke="#fff" stroke-width="1.5" fill="none"/></svg></span>
  </div>
</section>

<section class="team">
  <h2 class="abs section-title">MEET OUR TEAM</h2>
  <p>Class aptent taciti sociosqu ad litora torquent per conubia nostra, per inceptos himenaeos. Nulla nunc dui, tristique in semper vel, congue sed ligula. Nam dolor ligula, faucibus id sodales in, auctor fringill torquent per conubia nostra</p>
  <div class="abs btn-solid">FIND MORE ABOUT US</div>
  <div class="abs portrait" style="left:351px;background:linear-gradient(135deg,#b98f5e,#6b4a34 55%,#1f1c1e)" role="img" aria-label="Portrait of a team member in a dark suit"></div>
  <div class="abs portrait" style="left:609px;background:linear-gradient(180deg,#f2f2f2,#d9c9a8 45%,#2a2a2e)" role="img" aria-label="Portrait of a team member in a black blazer"></div>
  <div class="abs portrait" style="left:868px;background:linear-gradient(135deg,#e6eef3,#b8cbd8 50%,#f4f6f8)" role="img" aria-label="Team member at a desk in a bright office"></div>
</section>

<section class="sold">
  <div class="abs sold-col" style="left:98px">
    <h2 style="left:0">Previously Sold</h2>
    <span class="rule" style="left:140px;width:300px"></span>
    <div class="mini-nav" style="left:444px"><i></i><i></i></div>
    <div class="avatar" role="img" aria-label="Sold family home with green lawn" style="left:0;background:linear-gradient(180deg,#3a78d0,#8c7a66 55%,#4f8a32)"></div>
    <h3 style="left:157px">Righteous indignation</h3>
    <span class="date" style="left:325px">▦&nbsp; 25 March 2015</span>
    <p style="left:157px">Sed ut perspiciatis unde omnis iste natus error sit voluptatem accusantium doloremque laudantium, totam rem aperiam, eaque ipsa quae ab illo inventore veritatis et quasi architecto beatae vitae dicta sunt explicabo. Nemo enimtem</p>
  </div>
  <div class="abs sold-col" style="left:610px">
    <h2 style="left:0">List with the Leader</h2>
    <span class="rule" style="left:182px;width:244px"></span>
    <div class="mini-nav" style="left:462px"><i></i><i></i></div>
    <div class="avatar" role="img" aria-label="Portrait of the lead agent" style="left:20px;background:linear-gradient(135deg,#4a3a34,#8b6b58 50%,#2a2422)"></div>
    <h3 style="left:174px">Blanditiis praesentium</h3>
    <p style="left:174px">Sed ut perspiciatis unde omnis iste natus error sit voluptatem accusantium doloremque laudantium, totam rem aperiam, eaque ipsa quae ab illo inventore veritatis et quasi architecto beatae vitae dicta sunt explicabo. Nemo enimtem</p>
  </div>
</section>

<footer class="site-footer">
  <div class="social"><i></i><i></i><i></i></div>
  <nav class="footer-nav">Welcome&nbsp; /&nbsp; Featured Listings&nbsp; /&nbsp; Previously Sold&nbsp; /&nbsp; Sell&nbsp; /&nbsp; Property Search&nbsp; /&nbsp; Team&nbsp; /&nbsp; Videos&nbsp; /&nbsp; Blog&nbsp; /&nbsp; Explore O.C.&nbsp; /&nbsp; Contact</nav>
  <p class="copyright">Copyrights© Halden Studio.&nbsp; Allrights Reserved.&nbsp;&nbsp;&nbsp; Terms of use&nbsp;&nbsp; Privacy policy</p>
</footer>

</body>
</html>
```